Homemaking training schools needs a Business Card design

Designer, Hello!

No special requirements, good-looking enough.
--------------------------------------------------------------------------

Name: Marcus Dole
Chairman
Tel: 0574-71948263
Mobile: 13857420916
Email: kelvora@mailnest.example
Web: www.prt2019.example
Add: No.258, LanpingJie, BeiyuanQu, Ningbo, Zhejiang

LOGO
Ningbo PRT Homemaking Training School

Target Market(s)

pregnant women, mothers, infants, the elderly and families, including cleaning, cooking, nursing training.

Industry/Entity Type

Business

Contact Information for Business Card

Name: Marcus Dole
Chairman
Tel: 0574-71948263
Mobile: 13857420916
Email: kelvora@mailnest.example
Web: www.prt2019.example

LOGO

Font styles to use
Serif
Sans Serif
Decorative

Requirements
Nice to have
• Feels: clean, specifications, safety, comfort, warmth and happiness.

```html
<!DOCTYPE html>
<html lang="en">
<head>
<meta charset="utf-8">
<title>PeiRenTang Business Card</title>
<link href="https://fonts.googleapis.com/css2?family=Open+Sans:wght@400;600;700&display=swap" rel="stylesheet">
<style>
  :root {
    --page-bg: #2b2b2b;
    --card-bg: #121212;
    --card-edge: #1c1c1c;
    --accent-pink: #e0148c;
    --accent-blue: #1c78c0;
    --text-light: #f2f2f2;
    --text-muted: #9a9a9a;
    --divider: #333333;
  }
  * { box-sizing: border-box; margin: 0; padding: 0; }
  html, body {
    width: 1200px;
    height: 900px;
    overflow: hidden;
    background: var(--page-bg);
    font-family: "Open Sans", Arial, sans-serif;
  }
  .canvas {
    width: 1200px;
    height: 900px;
    display: flex;
    align-items: center;
    justify-content: center;
    gap: 40px;
  }
  .card {
    width: 540px;
    height: 310px;
    background: var(--card-bg);
    border: 1px solid var(--card-edge);
    border-radius: 22px;
    position: relative;
    overflow: hidden;
  }

  /* Contact side */
  .card-front { display: flex; }
  .front-brand {
    width: 46%;
    display: flex;
    align-items: center;
    justify-content: center;
    gap: 10px;
    border-right: 1px solid var(--divider);
    margin: 34px 0;
  }
  .brand-dot {
    width: 22px;
    height: 22px;
    border-radius: 50%;
    background: var(--accent-pink);
  }
  .brand-name {
    font-weight: 600;
    font-size: 26px;
    color: var(--accent-blue);
    letter-spacing: -0.3px;
  }
  .front-details {
    flex: 1;
    padding: 48px 20px 0 34px;
    color: var(--text-light);
  }
  .person-name {
    font-weight: 700;
    font-size: 19px;
    color: var(--accent-pink);
    line-height: 1.1;
  }
  .person-title {
    font-size: 13px;
    margin-top: 2px;
  }
  .address {
    font-size: 13.5px;
    line-height: 1.4;
    margin-top: 18px;
  }
  .contact-list {
    list-style: none;
    margin-top: 16px;
    font-size: 14px;
    line-height: 1.55;
  }
  .contact-list li {
    display: flex;
    align-items: center;
    gap: 9px;
  }
  .contact-icon {
    width: 12px;
    height: 12px;
    flex: none;
    fill: var(--accent-pink);
  }

  /* Logo side */
  .card-back {
    display: flex;
    flex-direction: column;
    align-items: center;
    justify-content: center;
  }
  .back-brand {
    display: flex;
    align-items: center;
    gap: 12px;
  }
  .back-brand .brand-dot { width: 18px; height: 18px; }
  .back-brand .brand-name { font-size: 38px; }
  .tagline-row {
    display: flex;
    align-items: center;
    gap: 10px;
    margin-top: 4px;
  }
  .tagline-rule {
    width: 72px;
    height: 1px;
    background: var(--text-muted);
  }
  .tagline {
    font-size: 14px;
    color: var(--text-muted);
    letter-spacing: 0.5px;
  }
</style>
</head>
<body>
  <main class="canvas">
    <section class="card card-front" aria-label="Business card, contact side">
      <div class="front-brand">
        <span class="brand-dot"></span>
        <span class="brand-name">PeiRenTang</span>
      </div>
      <div class="front-details">
        <h1 class="person-name">Marcus Dole</h1>
        <p class="person-title">Chairman</p>
        <p class="address">No.258, LanpingJie,<br>BeiyuanQu, Ningbo, Zhejiang</p>
        <ul class="contact-list">
          <li>
            <svg class="contact-icon" viewBox="0 0 12 12" aria-hidden="true"><path d="M2.5 0.8 L4.4 3 L3.4 4.3 C4 5.7 6.3 8 7.7 8.6 L9 7.6 L11.2 9.5 L9.8 11.2 C5.5 11 1 6.5 0.8 2.2 Z"/></svg>
            <span>0574-71948263</span>
          </li>
          <li>
            <svg class="contact-icon" viewBox="0 0 12 12" aria-hidden="true"><path d="M3 0.5 H9 V11.5 H3 Z M4.2 1.8 V9 H7.8 V1.8 Z"/></svg>
            <span>13857420916</span>
          </li>
          <li>
            <svg class="contact-icon" viewBox="0 0 12 12" aria-hidden="true"><path d="M0.5 2 H11.5 V10 H0.5 Z M1.8 3.2 L6 6.4 L10.2 3.2 Z"/></svg>
            <span>kelvora@mailnest.example</span>
          </li>
          <li>
            <svg class="contact-icon" viewBox="0 0 12 12" aria-hidden="true"><circle cx="6" cy="6" r="5.5"/><path d="M0.5 6 H11.5 M6 0.5 C3.5 3 3.5 9 6 11.5 C8.5 9 8.5 3 6 0.5" stroke="#121212" stroke-width="0.9" fill="none"/></svg>
            <span>www.prt2019.example</span>
          </li>
        </ul>
      </div>
    </section>

    <section class="card card-back" aria-label="Business card, brand side">
      <div class="back-brand">
        <span class="brand-dot"></span>
        <span class="brand-name">PeiRenTang</span>
      </div>
      <div class="tagline-row">
        <span class="tagline-rule"></span>
        <span class="tagline">Training &amp; Services</span>
        <span class="tagline-rule"></span>
      </div>
    </section>
  </main>
</body>
</html>
```